e-commerce store for sport clothing online store "baseball merchandise "web application...

I want to design a UX/UI for my web application website for the online store I will provide you with the following:
1. screen shots of the initial design for the pages>
2. the logo files.
3. The brand guideline file.

the provided files (screen shots) is guideline I want to see CREATIVITY with the UX/UI DESIGN.
PS. PLEASE FOLLOW THE BRANDGUIDE LINE CAREFULLY SPECIALLY THE TYPOGRAPHY & THE COLOR CODES.

PLEASE VISIT THIS WEBSITE brightlane.varomi-qz.com to see more for the screens.

```html
<!DOCTYPE html>
<html lang="en">
<head>
<meta charset="utf-8">
<title>Shopping Cart</title>
<link href="https://fonts.googleapis.com/css2?family=Mulish:wght@400;600;700;800&display=swap" rel="stylesheet">
<style>
:root{
  --navy:#0e2246;
  --navy-text:#1a2b4c;
  --red:#c8102e;
  --black:#000;
  --white:#fff;
  --card-border:#c9c9cf;
  --selected-bg:#c9c9c9;
  --text:#111;
}
*{box-sizing:border-box;margin:0;padding:0}
html,body{width:1200px;height:2667px;overflow:hidden;background:var(--white)}
body{font-family:'Mulish',sans-serif;color:var(--text)}
.canvas{position:relative;width:1200px;height:2667px;overflow:hidden}
.screen{position:absolute;left:0;top:0;width:360px;height:800px;overflow:hidden;transform:scale(3.33333);transform-origin:0 0;background:var(--white)}
.app-header{position:absolute;left:0;top:0;width:360px;height:82px;background:var(--navy)}
.app-header .back{position:absolute;left:23px;top:31px}
.app-header h1{position:absolute;left:0;right:0;top:30px;text-align:center;color:var(--white);font-size:16px;font-weight:800;word-spacing:3px}
.select-bar{position:absolute;left:0;top:89px;width:360px;height:24px}
.radio{position:absolute;width:19px;height:19px;border-radius:50%;border:1.5px solid #333;background:var(--white)}
.select-bar .radio{left:14px;top:2px}
.select-bar .all{position:absolute;left:43px;top:4px;font-size:14px}
.select-bar .count{position:absolute;right:62px;top:4px;font-size:13px;font-weight:700}
.select-bar .trash{position:absolute;left:322px;top:1px}
.cart-item{position:absolute;left:7px;width:346px;height:125px;border:1px solid var(--card-border);border-radius:5px;background:var(--white)}
.cart-item.is-selected{background:var(--selected-bg);border-color:#9a9a9a}
.cart-item .mark{position:absolute;left:6px;top:6px;width:21px;height:21px;border-radius:50%;z-index:2}
.mark.checked{background:var(--black)}
.mark.empty{background:#9b9b9b;border:1px solid #777}
.product-photo{position:absolute;border-radius:3px;box-shadow:0 1px 4px rgba(0,0,0,.3)}
.photo-trunks{left:20px;top:8px;width:88px;height:95px;background:linear-gradient(135deg,#5e9a72,#3f8a5c 60%,#7fb08c)}
.photo-cap{left:20px;top:19px;width:98px;height:83px;background:radial-gradient(ellipse at 50% 55%,#9fa3ad 0,#c7cad1 45%,#fdfdfd 85%)}
.product-name{position:absolute;left:126px;font-size:14px;font-weight:800;line-height:19px;width:150px}
.qty{position:absolute;left:126px;display:flex;align-items:center;gap:6px}
.qty .btn{width:17px;height:17px;border-radius:50%;display:flex;align-items:center;justify-content:center}
.qty .minus{border:1.5px solid #111;background:var(--white)}
.qty .plus{background:var(--navy)}
.qty .value{width:20px;height:18px;border:1px solid #999;font-size:13px;text-align:center;line-height:16px;background:#f4f4f4}
.price{position:absolute;right:12px;font-size:15px;font-weight:800;color:var(--navy-text)}
.voucher{position:absolute;left:13px;top:561px;width:247px;height:33px;border:1px solid #777;border-radius:3px;font-size:11px;padding:9px 10px;color:#111}
.apply{position:absolute;left:274px;top:560px;width:79px;height:35px;border-radius:4px;background:var(--navy);color:var(--white);font-size:14px;font-weight:700;text-align:center;line-height:35px}
.summary{position:absolute;left:20px;top:623px;width:320px}
.summary .row{display:flex;justify-content:space-between;height:27px;font-size:12.5px}
.summary .row span:last-child{color:var(--navy-text);font-weight:700}
.checkout-bar{position:absolute;left:2px;top:741px;width:356px;height:59px;background:var(--white);border-radius:12px 12px 0 0;box-shadow:0 -1px 6px rgba(0,0,0,.3)}
.checkout{position:absolute;left:12px;top:748px;width:336px;height:44px;background:var(--black);border-radius:4px;color:var(--white);font-size:14px;font-weight:800;text-align:center;line-height:44px}
</style>
</head>
<body>
<div class="canvas">
<div class="screen">
  <header class="app-header">
    <svg class="back" width="18" height="18" viewBox="0 0 18 18"><path d="M16 9H3M9 2.5L2.5 9 9 15.5" stroke="#fff" stroke-width="2.2" fill="none" stroke-linecap="round" stroke-linejoin="round"/></svg>
    <h1>Shopping Cart</h1>
  </header>

  <div class="select-bar">
    <span class="radio"></span>
    <span class="all">All</span>
    <span class="count">1 Selected</span>
    <svg class="trash" width="20" height="22" viewBox="0 0 20 22"><path d="M2 4h16M7 4V2h6v2M4 4l1 16h10l1-16M8 8v9M12 8v9" stroke="#c8102e" stroke-width="2" fill="none"/></svg>
  </div>

  <article class="cart-item is-selected" style="top:119px">
    <span class="mark checked"><svg width="21" height="21" viewBox="0 0 21 21"><path d="M6 11l3 3 6-7" stroke="#fff" stroke-width="2" fill="none"/></svg></span>
    <div class="product-photo photo-trunks" role="img" aria-label="Green printed kids swim trunks"></div>
    <h2 class="product-name" style="top:22px">Tidewave Kids Swim Trunks</h2>
    <div class="qty" style="top:76px">
      <span class="btn minus"><svg width="9" height="9"><path d="M1 4.5h7" stroke="#111" stroke-width="2"/></svg></span>
      <span class="value">1</span>
      <span class="btn plus"><svg width="9" height="9"><path d="M1 4.5h7M4.5 1v7" stroke="#fff" stroke-width="2"/></svg></span>
    </div>
    <span class="price" style="top:97px">23.000 KD</span>
  </article>

  <article class="cart-item" style="top:260px">
    <span class="mark empty"></span>
    <div class="product-photo photo-cap" role="img" aria-label="Grey trucker cap with fish patch"></div>
    <h2 class="product-name" style="top:21px">Bass Trucker Cap</h2>
    <div class="qty" style="top:76px">
      <span class="btn minus"><svg width="9" height="9"><path d="M1 4.5h7" stroke="#111" stroke-width="2"/></svg></span>
      <span class="value">2</span>
      <span class="btn plus"><svg width="9" height="9"><path d="M1 4.5h7M4.5 1v7" stroke="#fff" stroke-width="2"/></svg></span>
    </div>
    <span class="price" style="top:96px">13.000 KD</span>
  </article>

  <div class="voucher">Enter Voucher Code</div>
  <div class="apply">Apply</div>

  <section class="summary">
    <div class="row"><span>Subtotal</span><span>23.000 KD</span></div>
    <div class="row"><span>Delivery Charge</span><span>1.000 KD</span></div>
    <div class="row"><span>Total</span><span>24.000 KD</span></div>
  </section>

  <div class="checkout-bar"></div>
  <div class="checkout">Go to Checkout</div>
</div>
</div>
</body>
</html>
```